Local Roofing/Construction company business needs new biz card design

We need a new business card design, current cards are from the start of this operation and generic at best. We are a local Construction Company (General Contractor) with a majority of our work originating from insurance claims-exterior finish work is the main focus (Roofs-Siding-Gutters etc). Heavily involved with homeowners and the low ball offers they receive from insurance company's after a insurable event takes place. I have attached some of our original logo file(s) below.

```html
<!DOCTYPE html>
<html lang="en">
<head>
<meta charset="utf-8">
<title>Tallbridge Construction – Business Card</title>
<link rel="stylesheet" href="https://fonts.googleapis.com/css2?family=Open+Sans:wght@400;600;700&display=swap">
<style>
  :root {
    --page-bg: #d9d4cc;
    --card-bg: #e4d9c8;
    --ink-dark: #0f1f1d;
    --ink-text: #2a2a2a;
    --brand-green: #3fa652;
    --brand-green-deep: #2f8a3f;
    --brand-beige: #d8c9b2;
  }
  html, body {
    margin: 0;
    width: 1200px;
    height: 1046px;
    overflow: hidden;
    background: var(--page-bg);
    font-family: "Open Sans", sans-serif;
  }
  .business-card {
    position: absolute;
    left: 50px;
    top: 223px;
    width: 1100px;
    height: 600px;
    background: var(--card-bg);
    overflow: hidden;
    box-shadow: 0 10px 30px rgba(0,0,0,0.18);
  }
  .card-panel {
    position: absolute;
    inset: 0;
  }
  .brand-wordmark {
    position: absolute;
    left: 36px;
    top: 44px;
    display: flex;
    align-items: center;
    gap: 16px;
    color: var(--ink-dark);
    font-weight: 700;
    font-size: 40px;
    line-height: 1.05;
    letter-spacing: 1px;
  }
  .brand-square {
    width: 70px;
    height: 70px;
    background: var(--brand-green);
    flex: none;
  }
  .brand-wordmark small {
    display: block;
    font-size: 26px;
    letter-spacing: 3px;
  }
  .contact-block {
    position: absolute;
    left: 0;
    top: 208px;
  }
  .name-row {
    position: relative;
    padding-left: 36px;
  }
  .name-accent {
    position: absolute;
    left: 2px;
    top: 4px;
    width: 26px;
    height: 80px;
    background: var(--brand-green);
  }
  .person-name {
    margin: 0;
    font-size: 48px;
    font-weight: 700;
    line-height: 1.1;
    color: var(--ink-dark);
  }
  .person-name .first { color: var(--brand-green); }
  .person-title {
    margin: 0;
    font-size: 27px;
    font-weight: 400;
    color: var(--ink-text);
  }
  .address {
    margin: 30px 0 0 36px;
    font-style: normal;
    font-size: 27px;
    line-height: 36px;
    color: var(--ink-text);
  }
  .contact-list {
    list-style: none;
    margin: 26px 0 0 36px;
    padding: 0;
    font-size: 27px;
    line-height: 36px;
    color: var(--ink-text);
  }
  .contact-list li {
    display: flex;
    align-items: center;
    gap: 16px;
  }
  .contact-list svg {
    width: 24px;
    height: 24px;
    flex: none;
  }
  .panel-wordmark {
    position: absolute;
    left: 660px;
    width: 420px;
    top: 200px;
    text-align: center;
    color: var(--brand-beige);
    font-weight: 700;
    font-size: 52px;
    line-height: 1.1;
    letter-spacing: 2px;
  }
  .panel-wordmark span {
    display: block;
    font-size: 34px;
    letter-spacing: 4px;
  }
</style>
</head>
<body>
  <section class="business-card">
    <svg class="card-panel" width="1100" height="600" viewBox="0 0 1100 600" aria-hidden="true">
      <path fill="var(--ink-dark)" d="M586,0 C640,60 645,140 634,190 C620,270 560,340 572,440 C578,520 588,570 592,600 L1100,600 L1100,0 Z"/>
      <path fill="var(--brand-green-deep)" d="M596,0 C650,70 655,150 644,200 C630,280 575,350 588,440 C600,530 635,580 665,600 L1100,600 L1100,0 Z"/>
      <path fill="var(--ink-dark)" d="M602,0 C656,70 660,150 650,200 C636,280 590,350 604,440 C614,520 626,570 634,600 L1100,600 L1100,0 Z"/>
    </svg>

    <div class="brand-wordmark">
      <div class="brand-square"></div>
      <div>TALLBRIDGE<small>CONSTRUCTION</small></div>
    </div>

    <div class="contact-block">
      <div class="name-row">
        <div class="name-accent"></div>
        <h1 class="person-name"><span class="first">Marta</span> Kovalen</h1>
        <p class="person-title">Co-Founder</p>
      </div>
      <address class="address">245 Orchard Ridge Ln<br>Fairhaven, MO 63000</address>
      <ul class="contact-list">
        <li>
          <svg viewBox="0 0 24 24"><path fill="var(--brand-green)" d="M6.6 10.8a15 15 0 0 0 6.6 6.6l2.2-2.2a1 1 0 0 1 1-.25 11.4 11.4 0 0 0 3.6.57 1 1 0 0 1 1 1V20a1 1 0 0 1-1 1A17 17 0 0 1 3 4a1 1 0 0 1 1-1h3.5a1 1 0 0 1 1 1c0 1.25.2 2.45.57 3.57a1 1 0 0 1-.25 1z"/></svg>
          555-214-3087
        </li>
        <li>
          <svg viewBox="0 0 24 24"><path fill="var(--brand-green)" d="M6.6 10.8a15 15 0 0 0 6.6 6.6l2.2-2.2a1 1 0 0 1 1-.25 11.4 11.4 0 0 0 3.6.57 1 1 0 0 1 1 1V20a1 1 0 0 1-1 1A17 17 0 0 1 3 4a1 1 0 0 1 1-1h3.5a1 1 0 0 1 1 1c0 1.25.2 2.45.57 3.57a1 1 0 0 1-.25 1z"/></svg>
          555-619-2740 (Emergency)
        </li>
        <li>
          <svg viewBox="0 0 24 24"><circle cx="12" cy="12" r="10" fill="var(--brand-green)"/><path d="M2 12h20M12 2c3 3 3 17 0 20M12 2c-3 3-3 17 0 20" stroke="var(--card-bg)" stroke-width="1.4" fill="none"/></svg>
          www.tallbridgebuild.com
        </li>
        <li>
          <svg viewBox="0 0 24 24"><rect x="2" y="5" width="20" height="14" fill="var(--brand-green)"/><path d="M2 5l10 8 10-8" stroke="var(--card-bg)" stroke-width="1.5" fill="none"/></svg>
          crew@tallbridgebuild.com
        </li>
      </ul>
    </div>

    <div class="panel-wordmark">TALLBRIDGE<span>CONSTRUCTION</span></div>
  </section>
</body>
</html>
```